Wordpress 6 pages GLAM design for hair salon

Hi guys.
I need a glam & easy to navigate web design for my (women only) new hair salon.
I have a logo. You can see in attached files.
I like 3d backgrounds.
My favourite colours choice: any variety of pink(hot & very soft), white, black, grey.
I would like to see website very feminine, glamorous & kind of old Hollywood and Dorinda Calloway inspired.
Of course it should have plug ins, like social media, map, security etc.
My website now: http://velmoracoiffure.example

Designs what I like:
http://torvinellastudio.example
http://pelurabeautyloft.example
http://www.quillfernvisualworks.example/boutique-graphic-web-folio.html
Updates

Target Market(s)

WOMEN

Industry/Entity Type

Boutique

Requirements
Should not have
• any cartoon or other characters!

```html
<!DOCTYPE html>
<html lang="en">
<head>
<meta charset="utf-8">
<title>Velmora Coiffure</title>
<link href="https://fonts.googleapis.com/css2?family=Cinzel:wght@400&family=Arimo:wght@400&display=swap" rel="stylesheet">
<style>
:root{
  --pink:#c84a7c;
  --pink-dark:#9c1447;
  --pink-soft:#e07aa2;
  --text:#8a8a8a;
  --white:#fff;
  --footer:#3b3b3b;
  --leather-a:#a8611f;
  --leather-b:#6a3510;
}
*{margin:0;padding:0;box-sizing:border-box}
html,body{width:774px;height:1200px;overflow:hidden}
body{position:relative;font-family:"Arimo",Arial,sans-serif;background:var(--leather-b)}
.abs{position:absolute}
.backdrop{left:0;top:0;width:774px;height:1200px;
  background:radial-gradient(circle at 20% 15%,#c98439 0,var(--leather-a) 25%,var(--leather-b) 60%),var(--leather-b)}
.brand{left:287px;top:34px;width:200px;text-align:center;display:flex;flex-direction:column;align-items:center;gap:4px}
.brand-dot{width:14px;height:14px;border-radius:50%;background:var(--pink)}
.brand-name{font-family:"Cinzel",serif;font-size:17px;color:var(--white);letter-spacing:1px;line-height:1.1}
.nav{left:90px;top:105px;width:593px;height:26px;background:var(--pink);display:flex;align-items:center}
.nav a{color:var(--white);font-size:9.5px;text-decoration:none;margin-left:24px;margin-right:11px}
.search{position:absolute;right:6px;top:5px;width:122px;height:17px;background:#f6e3ec;border-radius:3px;font-size:6.5px;color:#777;padding:5px 0 0 8px}
.search svg{position:absolute;right:7px;top:4px}
.hero{left:90px;top:131px;width:593px;height:290px;background:linear-gradient(100deg,#5a2612 0%,#a1522a 35%,#c9804f 55%,#f1e2da 75%,#fff 100%)}
.hero-title{left:218px;top:276px;font-family:"Cinzel",serif;font-size:15px;color:var(--white);letter-spacing:.5px}
.hero-text{left:218px;top:306px;width:240px;font-size:8.3px;line-height:17px;color:var(--white)}
.hero-next{left:650px;top:245px}
.sheet{left:90px;top:421px;width:593px;height:717px;background:var(--white)}
.heading{font-family:"Cinzel",serif;font-size:15px;color:var(--pink);letter-spacing:.5px}
.photo{background:linear-gradient(135deg,#e8e8e8,#a89080 50%,#5a4030)}
.body-copy{font-size:7.6px;line-height:15.2px;color:var(--text)}
.btn{background:linear-gradient(#dd7ba0,var(--pink));color:var(--white);font-size:9px;display:flex;align-items:center;justify-content:center;border-radius:3px}
.rule{left:90px;width:593px;height:1px;background:#ddd}
.post-thumb{left:90px;width:72px;height:68px}
.post-text{left:179px;width:235px;font-size:7px;line-height:14.4px;color:var(--text)}
.post-date{left:180px;font-size:8px;color:var(--pink)}
.hours{left:468px;top:695px;width:216px;height:213px;background:var(--pink)}
.cal{left:2px;top:3px;width:128px;background:#f2f2f2;border:1px solid #bbb}
.cal-head{height:18px;background:#444;color:#fff;font-size:7.5px;display:flex;align-items:center;justify-content:space-between;padding:0 6px}
.cal-days{display:grid;grid-template-columns:repeat(7,1fr);font-size:4.5px;color:#555;text-align:center;padding:3px 0 1px}
.cal-grid{display:grid;grid-template-columns:repeat(7,1fr);gap:1px;padding:1px}
.cal-grid span{height:17px;background:#fafafa;border:1px solid #ccc;font-size:6.5px;color:#333;display:flex;align-items:center;justify-content:center}
.cal-grid .muted{color:#bbb}
.cal-grid .today{background:#5ab0c8;color:#fff}
.hours-times{left:142px;top:11px;color:var(--white);font-size:10px;line-height:13px}
.hours-note{left:2px;top:137px;width:212px;color:var(--white);font-size:6.6px;line-height:10.5px}
.hours-btn{left:34px;top:163px;width:145px;height:28px;background:var(--pink-dark);color:var(--white);font-size:8.5px;display:flex;align-items:center;justify-content:center;border-radius:3px}
.gallery-item{top:996px;width:118px;height:103px}
.footer{left:0;top:1138px;width:774px;height:62px;background:var(--footer)}
.footer-nav{left:0;top:18px;width:774px;text-align:center;font-size:7.2px;color:var(--white)}
.footer-nav span{margin:0 6px}
.copyright{left:0;top:37px;width:774px;text-align:center;font-size:7px;color:var(--white)}
</style>
</head>
<body>
<div class="abs backdrop" role="img" aria-label="Tufted brown leather upholstery background"></div>

<div class="abs brand"><span class="brand-dot"></span><span class="brand-name">Velmora Coiffure</span></div>

<nav class="abs nav">
  <a>Home</a><a>About us</a><a>Services</a><a>Gallery</a><a>Blog</a><a>Contacts</a>
  <div class="search">Search
    <svg width="11" height="9" viewBox="0 0 11 9"><circle cx="4" cy="4" r="3" fill="none" stroke="#999" stroke-width="1.2"/><line x1="6.2" y1="6" x2="10" y2="8.5" stroke="#999" stroke-width="1.4"/></svg>
  </div>
</nav>

<div class="abs hero" role="img" aria-label="Woman with long flowing auburn hair"></div>
<div class="abs hero-title">Velmora Coiffure</div>
<p class="abs hero-text">Our salon is based on the belief that our customer's needs are of the utmost importance. Our team is committed to meet-ing those needs</p>
<svg class="abs hero-next" width="20" height="20" viewBox="0 0 20 20"><circle cx="10" cy="10" r="9" fill="none" stroke="#e9c6d3" stroke-width="1.4"/><path d="M8 5.5 L13 10 L8 14.5" fill="none" stroke="#e9c6d3" stroke-width="1.4"/></svg>

<div class="abs sheet"></div>

<h2 class="abs heading" style="left:93px;top:440px">Welcome to Hair Studio</h2>
<div class="abs photo" style="left:90px;top:472px;width:207px;height:156px" role="img" aria-label="Portrait of a woman with windswept light brown hair"></div>
<p class="abs body-copy" style="left:322px;top:471px;width:352px">Our salon is based on the belief that our customer's needs are of the utmost importance. Our team is committed to meeting those needs.As a result,a high percentage of our business is from report cus-tomer and referrals.Our salon is based on the belief that our customer's needs are of the utmost importance. Our team is committed to meeting those needs.As a result,a high percentage of our busi-ness is from report customer and referrals.Our salon is based on the belief that our customer's needs are of the utmost importance. &nbsp;Our team is committed to meeting those needs.As a result, &nbsp;is from report customer and referrals.</p>
<div class="abs btn" style="left:322px;top:603px;width:81px;height:23px">Click here</div>

<div class="abs rule" style="top:649px"></div>

<h2 class="abs heading" style="left:91px;top:661px">Recent Posts</h2>

<div class="abs post-thumb photo" style="top:696px" role="img" aria-label="Woman with curly blonde hair"></div>
<p class="abs post-text" style="top:695px">Our salon is based on the belief that our customer's needs are of the utmost importance. Our team is committed to meeting those needs.As a result,a high percentage of our business is from report customer ...</p>
<div class="abs post-date" style="top:750px">December 14,2013</div>

<div class="abs post-thumb" style="top:784px;background:linear-gradient(135deg,#d9b8b0,#7a3a30 60%,#3a1a18)" role="img" aria-label="Woman with long sleek brown hair"></div>
<p class="abs post-text" style="top:783px">Our salon is based on the belief that our customer's needs are of the utmost importance. Our team is committed to meeting those needs.As a result,a high percentage of our business is from report customer ...</p>
<div class="abs post-date" style="top:838px">December 14,2013</div>

<div class="abs post-thumb" style="top:870px;background:linear-gradient(90deg,#f3ece8,#8a5a40 45%,#f3ece8)" role="img" aria-label="Woman with straight dark hair"></div>
<p class="abs post-text" style="top:869px">Our salon is based on the belief that our customer's needs are of the utmost importance. Our team is committed to meeting those needs.As a result,a high percentage of our business is from report customer ...</p>
<div class="abs post-date" style="top:923px">December 14,2013</div>

<h2 class="abs heading" style="left:470px;top:661px">Working Hours</h2>
<div class="abs hours">
  <div class="abs cal">
    <div class="cal-head"><span>◂</span><span>January 2014</span><span>▸</span></div>
    <div class="cal-days"><span>MON</span><span>TUE</span><span>WED</span><span>THU</span><span>FRI</span><span>SAT</span><span>SUN</span></div>
    <div class="cal-grid">
      <span class="muted">28</span><span>1</span><span>2</span><span>3</span><span class="today">4</span><span>5</span><span>6</span>
      <span>7</span><span>8</span><span>9</span><span>10</span><span>11</span><span>12</span><span>13</span>
      <span>14</span><span>15</span><span>16</span><span>17</span><span>18</span><span>19</span><span>20</span>
      <span>21</span><span>22</span><span>23</span><span>24</span><span>25</span><span>26</span><span>27</span>
      <span>28</span><span>29</span><span>30</span><span>31</span><span class="muted">1</span><span class="muted">2</span><span class="muted">3</span>
    </div>
  </div>
  <div class="abs hours-times">Sunday 12-5<br><br style="line-height:8px">Monday to<br>Satirday 9-6</div>
  <p class="abs hours-note">Our salon is based on the belief that our customer's needs are of the utmost importance.</p>
  <div class="abs hours-btn">Booking on one day before</div>
</div>

<div class="abs rule" style="top:961px"></div>

<h2 class="abs heading" style="left:91px;top:969px">Our Gallery</h2>
<svg class="abs" style="left:660px;top:973px" width="22" height="12" viewBox="0 0 22 12"><path d="M6 1 L1 6 L6 11" fill="none" stroke="#aaa" stroke-width="1.2"/><path d="M16 1 L21 6 L16 11" fill="none" stroke="#aaa" stroke-width="1.2"/></svg>

<div class="abs gallery-item" style="left:90px;background:linear-gradient(135deg,#e3c08a,#a07040 60%,#5a3a20)" role="img" aria-label="Woman with wavy blonde hair"></div>
<div class="abs gallery-item" style="left:209px;background:linear-gradient(135deg,#f2f2f2,#6a4030 55%,#2a1a14)" role="img" aria-label="Woman with short dark bob"></div>
<div class="abs gallery-item" style="left:328px;background:linear-gradient(135deg,#4a1020,#8a2035 50%,#c05a70)" role="img" aria-label="Woman with deep red hair"></div>
<div class="abs gallery-item" style="left:447px;background:linear-gradient(135deg,#fff,#6a4a38 55%,#3a2418)" role="img" aria-label="Woman with voluminous brunette waves"></div>
<div class="abs gallery-item" style="left:565px;background:linear-gradient(135deg,#d8d8d8,#4a3428 55%,#2a1a12)" role="img" aria-label="Woman with windblown dark hair"></div>

<footer class="abs footer">
  <div class="abs footer-nav">Home<span>|</span>About us<span>|</span>Services<span>|</span>Gallery<span>|</span>Blog<span>|</span>Contacts</div>
  <div class="abs copyright">Copyright 2014 Velmora Coiffure.All Right Reseved.</div>
</footer>
</body>
</html>
```